Every Shelf Set Neatly or ESN Organized needs a business card design. ESN Organized is a professi

We need a business card design that is clean, sharp and conveys a sense of organization. I already have a logo.

Target Market(s)

Families (specifically mothers), small business owners, parents, seniors

Industry/Entity Type

Business

Contact Information for Business Card

My website is www.esnorganized-example.com and my Facebook page is http://www.sociallink-example.com/everyshelfsetneatly. The phone number is 418-552-7094 and I want to be listed as Lorna M. Pelham, Owner

Requirements
Must have
• My logo.

```html
<!DOCTYPE html>
<html lang="en">
<head>
<meta charset="utf-8">
<title>ESN Organized – Business Card</title>
<link rel="stylesheet" href="https://fonts.googleapis.com/css2?family=Montserrat:wght@400;600&family=Open+Sans:wght@400;600;700&display=swap">
<style>
  :root {
    --brand-blue: #0b78d8;
    --brand-blue-deep: #0a67bb;
    --ink: #1c1c1c;
    --paper: #ffffff;
    --stage: #e6e8eb;
    --faint: rgba(0, 40, 90, 0.13);
  }
  * { box-sizing: border-box; margin: 0; padding: 0; }
  html, body {
    width: 1200px; height: 864px; overflow: hidden;
    background: var(--stage);
  }
  .stage {
    width: 1200px; height: 864px;
    display: flex; flex-direction: column;
    align-items: center; justify-content: center; gap: 40px;
  }
  .card {
    position: relative;
    width: 560px; height: 320px;
    overflow: hidden;
    box-shadow: 0 6px 18px rgba(0,0,0,0.18);
  }

  /* Front */
  .card--front { background: var(--brand-blue); }
  .front__decor {
    position: absolute; left: 10px; top: -30px;
    font-family: "Montserrat", sans-serif; font-weight: 400;
    font-size: 260px; letter-spacing: 10px; line-height: 1;
    color: var(--faint);
    white-space: nowrap;
  }
  .front__name {
    position: absolute; left: 0; right: 0; top: 96px;
    text-align: center;
    font-family: "Montserrat", sans-serif; font-weight: 400;
    font-size: 32px; letter-spacing: 5px; line-height: 1.25;
    color: var(--paper);
  }
  .front__band {
    position: absolute; left: 0; right: 0; top: 228px; height: 48px;
    background: var(--paper);
    display: flex; align-items: center; justify-content: center;
  }
  .front__social {
    font-family: "Open Sans", sans-serif; font-weight: 700;
    font-size: 13.5px; color: var(--brand-blue-deep);
  }

  /* Back */
  .card--back { background: var(--paper); }
  .back__brand {
    position: absolute; right: 38px; top: 48px;
    display: flex; align-items: center; gap: 12px;
  }
  .brand__dot {
    width: 14px; height: 14px; border-radius: 50%;
    background: var(--brand-blue);
  }
  .brand__name {
    font-family: "Montserrat", sans-serif; font-weight: 400;
    font-size: 25px; letter-spacing: 3px;
    color: var(--ink);
  }
  .back__person {
    position: absolute; left: 34px; top: 120px;
    font-family: "Open Sans", sans-serif;
  }
  .person__name {
    font-weight: 700; font-size: 19px; color: var(--brand-blue);
  }
  .person__role {
    font-size: 12.5px; color: var(--ink); margin-top: 1px;
  }
  .back__rule {
    position: absolute; left: 0; right: 0; top: 176px;
    height: 2px; background: var(--brand-blue);
  }
  .back__contacts {
    position: absolute; right: 28px; top: 212px;
    list-style: none;
    font-family: "Open Sans", sans-serif; font-size: 15px;
    color: var(--ink); text-align: right;
  }
  .contact {
    display: flex; align-items: center; justify-content: flex-end;
    gap: 8px; line-height: 25px;
  }
  .contact__icon { width: 13px; height: 13px; fill: var(--brand-blue); flex: none; }
</style>
</head>
<body>
<main class="stage">

  <section class="card card--front" aria-label="Business card front">
    <div class="front__decor" aria-hidden="true">ESN</div>
    <h1 class="front__name">Every Shelf<br>Set Neatly</h1>
    <div class="front__band">
      <span class="front__social">www.sociallink-example.com/everyshelfsetneatly</span>
    </div>
  </section>

  <section class="card card--back" aria-label="Business card back">
    <div class="back__brand">
      <span class="brand__dot" aria-hidden="true"></span>
      <span class="brand__name">Every Shelf Set Neatly</span>
    </div>
    <div class="back__person">
      <p class="person__name">Lorna M. Pelham</p>
      <p class="person__role">Owner</p>
    </div>
    <div class="back__rule"></div>
    <ul class="back__contacts">
      <li class="contact">418-552-7094
        <svg class="contact__icon" viewBox="0 0 16 16" aria-hidden="true"><path d="M3.6 1.2l2.3 2.6-1.2 1.9c.9 2 2.6 3.7 4.6 4.6l1.9-1.2 2.6 2.3-1.4 2.4C7.3 13.6 2.4 8.7 1.2 3z"/></svg>
      </li>
      <li class="contact">info@esnorganized-example.com
        <svg class="contact__icon" viewBox="0 0 16 16" aria-hidden="true"><path d="M1 3.5h14v9H1z M1.6 4l6.4 5 6.4-5" fill="var(--brand-blue)" stroke="#fff" stroke-width="1.1"/></svg>
      </li>
      <li class="contact">www.esnorganized-example.com
        <svg class="contact__icon" viewBox="0 0 16 16" aria-hidden="true"><circle cx="8" cy="8" r="7"/><path d="M1 8h14M8 1c-3 3.5-3 10.5 0 14M8 1c3 3.5 3 10.5 0 14" fill="none" stroke="#fff" stroke-width="1"/></svg>
      </li>
    </ul>
  </section>

</main>
</body>
</html>
```